Medical Clinic Group Looking for Website Design

We own and operate medical clinics and are looking looking to revamp our website. Our current website is www.brightpathcareclinics.ca We need our website to be more functional, user friendly, and easier to maintain.

```html
<!DOCTYPE html>
<html lang="en">
<head>
<meta charset="utf-8">
<title>Brightpath Care Clinics</title>
<link href="https://fonts.googleapis.com/css2?family=Roboto:wght@400;500;700&display=swap" rel="stylesheet">
<style>
:root{
  --teal:#2fcbdc;
  --teal-bright:#33d3dd;
  --teal-soft:#e6f8fa;
  --ink:#222;
  --grey:#6f6f72;
  --white:#fff;
  --footer-low:#7d8a90;
}
*{margin:0;padding:0;box-sizing:border-box}
html,body{width:1200px;height:2656px;overflow:hidden;background:var(--white);font-family:'Roboto',sans-serif;color:var(--ink)}
.page{position:relative;width:1200px;height:2656px}
.abs{position:absolute}

/* header */
.brand{position:absolute;display:flex;align-items:center;gap:12px}
.brand-dot{width:34px;height:34px;border-radius:50%;background:var(--teal)}
.brand-name{font-size:34px;font-weight:400;color:var(--teal);letter-spacing:.5px}
.site-header .brand{left:113px;top:26px}
.main-nav{position:absolute;top:40px;right:110px;display:flex;gap:27px;font-size:14px;font-weight:500}
.main-nav a{color:var(--ink);text-decoration:none}
.main-nav .current{color:var(--teal);border-bottom:2px solid var(--teal);padding-bottom:8px}
.main-nav .book{color:var(--teal);text-decoration:underline}

/* hero */
.hero{position:absolute;left:0;top:93px;width:1200px;height:643px;border-radius:180px 180px 0 120px;overflow:hidden;
  background:linear-gradient(100deg,#6d7378 0%,#9aa3a6 30%,#c9cfd0 50%,#e6e8e8 68%,#aab3b8 100%)}
.hero-photo{position:absolute;inset:0;background:radial-gradient(ellipse 280px 360px at 800px 330px,rgba(245,240,236,.85),rgba(255,255,255,0) 70%),
  radial-gradient(ellipse 220px 160px at 150px 560px,rgba(40,90,170,.55),rgba(0,0,0,0) 70%)}
.hero-kicker{left:103px;top:186px;font-size:20px;font-weight:500;color:var(--white)}
.hero-title{left:101px;top:220px;font-size:68px;line-height:78px;font-weight:500;color:var(--white)}
.btn{display:inline-flex;align-items:center;justify-content:center;gap:6px;border-radius:23px;font-size:14px;font-weight:700;text-transform:uppercase}
.btn-arrow{width:13px;height:13px;border-radius:50%;display:inline-flex;align-items:center;justify-content:center;font-size:9px}
.hero-cta{left:103px;top:390px;width:165px;height:45px;background:var(--teal);color:var(--white)}
.hero-cta .btn-arrow{background:var(--white);color:var(--teal)}
.hero-dots{left:103px;top:552px;display:flex;gap:8px}
.hero-dots span{width:12px;height:12px;border-radius:50%;background:var(--white)}
.hero-dots span:first-child{background:var(--teal)}
.scroll-down{left:581px;top:717px;width:38px;height:38px;border-radius:50%;background:var(--white);display:flex;align-items:center;justify-content:center}

/* quick tiles */
.tile{position:absolute;width:240px;text-align:center}
.tile svg{display:block;margin:0 auto}
.tile-label{margin-top:14px;font-size:14px;font-weight:500;text-transform:uppercase}

/* about */
.about{position:absolute;left:0;top:1335px;width:1200px;height:419px;background:linear-gradient(120deg,#2cc8da,#33d6e0 60%,#2bc6d9);text-align:center;color:var(--white)}
.about h2{position:absolute;left:0;right:0;top:95px;font-size:39px;font-weight:500}
.about p{position:absolute;left:195px;width:810px;top:158px;font-size:15.5px;font-weight:500;line-height:26px}
.about-cta{position:absolute;left:513px;top:259px;width:166px;height:44px;background:var(--white);color:var(--teal)}
.about-cta .btn-arrow{background:var(--teal);color:var(--white)}

/* connect */
.connect{position:absolute;left:0;right:0;top:1850px;text-align:center;font-size:26px;line-height:34px}
.contact-chip{position:absolute;top:2000px;display:flex;align-items:center;gap:14px;font-size:14.5px;line-height:26px}
.contact-chip b{font-weight:500}
.chip-icon{width:56px;height:56px;border-radius:50%;background:var(--teal);display:flex;align-items:center;justify-content:center}

/* footer */
.site-footer{position:absolute;left:0;top:2159px;width:1200px;height:497px;border-radius:120px 120px 0 170px;
  background:linear-gradient(180deg,var(--teal-bright) 0%,#3fc4cf 40%,var(--footer-low) 100%);color:var(--white)}
.news-title{left:217px;top:76px;font-size:26px;font-weight:700;letter-spacing:-.3px}
.news-field{left:602px;top:70px;width:380px;height:40px;background:var(--white);display:flex;align-items:center;justify-content:space-between;padding:0 14px;font-size:14px;color:var(--grey)}
.site-footer .brand{left:111px;top:198px}
.site-footer .brand-dot{background:var(--white)}
.site-footer .brand-name{color:var(--white)}
.foot-col{position:absolute;top:176px}
.foot-col h3{font-size:21px;font-weight:700;margin-bottom:14px}
.foot-col li{list-style:none;display:flex;align-items:center;gap:16px;font-size:14.5px;height:25.7px}
.foot-col li i{width:9px;height:9px;border-radius:50%;background:rgba(255,255,255,.55);display:inline-block;margin-left:3px}
.copyright{left:0;right:0;top:411px;text-align:center;font-size:13.5px}
</style>
</head>
<body>
<div class="page">

<header class="site-header">
  <div class="brand"><span class="brand-dot"></span><span class="brand-name">brightpath</span></div>
  <nav class="main-nav">
    <a class="current" href="#">Home</a><a href="#">Locations</a><a href="#">For Patients</a><a href="#">For Providers</a><a href="#">About Us</a><a class="book" href="#">Book Online</a>
  </nav>
</header>

<section class="hero">
  <div class="hero-photo" role="img" aria-label="Smiling doctor in a white coat holding a tablet in a bright clinic"></div>
  <p class="abs hero-kicker">WE'RE RENOVATING TO SERVE YOU BETTER</p>
  <h1 class="abs hero-title">Exciting Things<br>Are Happening!</h1>
  <a class="abs btn hero-cta">Get Started <span class="btn-arrow">&#10148;</span></a>
  <div class="abs hero-dots"><span></span><span></span><span></span><span></span></div>
</section>
<div class="abs scroll-down"><svg width="16" height="22" viewBox="0 0 16 22"><path d="M8 2v17M2 13l6 6 6-6" fill="none" stroke="#222" stroke-width="2"/></svg></div>

<svg width="0" height="0" style="position:absolute">
  <defs>
    <g id="tile-frame">
      <circle cx="82" cy="70" r="64" fill="#e6f8fa" stroke="#2fcbdc" stroke-width="2.5"/>
    </g>
  </defs>
</svg>

<div class="tile" style="left:153px;top:840px">
  <svg width="164" height="140"><use href="#tile-frame"/><g fill="none" stroke="#6f6f72" stroke-width="1.6"><circle cx="78" cy="52" r="10"/><path d="M58 96v-14q0-12 20-14q20 2 20 14"/><rect x="76" y="80" width="26" height="16"/><path d="M70 98h36"/></g></svg>
  <p class="tile-label">Find a Provider</p>
</div>
<div class="tile" style="left:481px;top:840px">
  <svg width="164" height="140"><use href="#tile-frame"/><g fill="none" stroke="#6f6f72" stroke-width="1.6"><circle cx="82" cy="70" r="24" stroke-dasharray="10 4"/><circle cx="82" cy="70" r="14"/><circle cx="82" cy="70" r="6"/></g></svg>
  <p class="tile-label">Services</p>
</div>
<div class="tile" style="left:809px;top:840px">
  <svg width="164" height="140"><use href="#tile-frame"/><g fill="none" stroke="#6f6f72" stroke-width="1.6"><rect x="56" y="46" width="46" height="44"/><path d="M56 58h46M64 66h8M76 66h8M64 76h8M76 76h8"/><circle cx="100" cy="88" r="12" fill="#fff"/><path d="M100 81v7h6"/></g></svg>
  <p class="tile-label">Book an Appointment</p>
</div>
<div class="tile" style="left:153px;top:1063px">
  <svg width="164" height="140"><use href="#tile-frame"/><g fill="none" stroke="#6f6f72" stroke-width="1.6"><path d="M82 92q-16-22-16-34a16 16 0 0 1 32 0q0 12-16 34z"/><circle cx="82" cy="57" r="6"/><path d="M64 84l-14 14h64l-14-14"/></g></svg>
  <p class="tile-label">Locations</p>
</div>
<div class="tile" style="left:481px;top:1063px">
  <svg width="164" height="140"><use href="#tile-frame"/><g fill="none" stroke="#6f6f72" stroke-width="1.6"><rect x="64" y="44" width="34" height="32"/><path d="M56 66h50v32H56z"/><path d="M81 72v20M71 82h20"/></g></svg>
  <p class="tile-label">Patient Resources</p>
</div>
<div class="tile" style="left:809px;top:1063px">
  <svg width="164" height="140"><use href="#tile-frame"/><g fill="none" stroke="#6f6f72" stroke-width="1.6"><rect x="70" y="44" width="40" height="30"/><path d="M70 44l20 16 20-16"/><path d="M58 66q-4 14 10 26t22 6l-6-8-6 4q-8-6-10-14l4-6-8-6z"/></g></svg>
  <p class="tile-label">Contact Us</p>
</div>

<section class="about">
  <h2>ABOUT US</h2>
  <p>At Brightpath Care Clinics, work/life balance is at the core of our culture. Our philosophy is simple: we take exceptional care of our people so that they can take exceptional care of our patients. Contact us to find out why so many healthcare providers and medical professionals have chosen to join our team.</p>
  <a class="btn about-cta">Learn More <span class="btn-arrow">&#10148;</span></a>
</section>

<p class="connect">Brightpath Care Clinics is focused on our patients first.<br>Connect &nbsp;with us to stay up to date with current<br>news and upcoming events.</p>

<div class="contact-chip" style="left:372px">
  <span class="chip-icon"><svg width="18" height="13"><rect x="0" y="0" width="18" height="13" fill="#fff"/><path d="M0 0l9 7 9-7" fill="none" stroke="#2fcbdc" stroke-width="1.4"/></svg></span>
  <div><b>Email :</b><br>hello@brightpathcareclinics.ca</div>
</div>
<div class="contact-chip" style="left:665px">
  <span class="chip-icon"><svg width="16" height="16" viewBox="0 0 16 16"><path d="M3 1q-3 8 3 12t9 2l-2-4-4 1q-4-2-5-6l3-2z" fill="#fff"/></svg></span>
  <div><b>Phone :</b><br>604.555.0172</div>
</div>

<footer class="site-footer">
  <h2 class="abs news-title">SUBSCRIBE OUR NEWSLETTER</h2>
  <div class="abs news-field"><span>Email address</span><svg width="16" height="14" viewBox="0 0 16 14"><path d="M1 6l14-5-4 12-3-5z" fill="#2fcbdc"/></svg></div>
  <div class="brand"><span class="brand-dot"></span><span class="brand-name">brightpath</span></div>

  <div class="foot-col" style="left:467px"><h3>Quick Links</h3><ul>
    <li><i></i>Home</li><li><i></i>About us</li><li><i></i>Services</li><li><i></i>Reviews</li><li><i></i>Contact us</li></ul></div>
  <div class="foot-col" style="left:690px"><h3>Contact us</h3><ul>
    <li><i></i>123,Lorem ipsum dolor sit</li><li></li><li><i></i>604.555.0172</li><li></li><li><i></i>hello@brightpathcareclinics.ca</li></ul></div>
  <div class="foot-col" style="left:990px"><h3>Follow us</h3><ul>
    <li><i></i>Photo Journal</li><li><i></i>Community Page</li><li><i></i>Clinic Updates</li><li><i></i>Video Library</li><li><i></i>Health Boards</li></ul></div>

  <p class="abs copyright">© Copyrights 2022 The Company Name | All Rights Reserved</p>
</footer>

</div>
</body>
</html>
```